Association qui souhaite améliorer l'accès aux personnes en situation de handicap

Nous sommes une association qui a pour objectif d'améliorer l'accessibilité, augmenter l'offre des activités réalisables dans notre région touristique.
Nous souhaitons réaliser un site internet afin de pouvoir communiquer sur notre association. Nous avons déjà conçu notre flyer sur Plumotrix. Nous souhaiterions une base graphique se rapportant à celui-ci. C'est possible de tout retravailler mais nous souhaitons tout de même retrouver la charte graphique ou code couleur du flyer.
Il nous faudrait quelques pages:
- 1 page : Acceuil / Présentation (Home), Il y aurait le descriptif de l'association, avec ses objectifs à +/- moyen terme
- 1 page : Nos réalisations, celle-ci présenterait les éléments que nous avons réalisés avec des zones de textes et des images classées chronologiquement au fur et à mesure des nouveautés
- 1 page : Media, comme la précédente, mais ou on pourrait voir ou lire sur les divers médias qui parlent de nous
- 1 page : Evenements : c'est une page pour présenter divers activités que nous allons organiser
- 1 page : Contact qui indique comment nous contacter et avec la présentation des 5 ou 6 membres du comité
- 1 link donate : qui arrive sur un formulaire de donnée que l'on pourra faire évoluer sur un système de payement par la suite. Cette bannière doit se retrouver sur toutes les pages
Il est nécessaire que se design puisse être transféré sur une lecture sur téléphone mobile
Personnes en situation de handicap
Associatif

```html
<!DOCTYPE html>
<html lang="en">
<head>
<meta charset="utf-8">
<title>Contact – Valpas Alliance</title>
<link rel="stylesheet" href="https://fonts.googleapis.com/css2?family=Raleway:wght@500;600;700&family=Kumbh+Sans:wght@400;500;600&family=Oswald:wght@500&family=Roboto:wght@400;500&display=swap">
<style>
:root{
  --red:#be1a27;
  --ink:#1d1d1f;
  --text:#333;
  --muted:#666;
  --soft:#f4f6fa;
  --line:#2b2b2b;
  --dark:#262d30;
  --white:#fff;
}
*{margin:0;padding:0;box-sizing:border-box}
html,body{width:1200px;height:2179px;overflow:hidden}
body{position:relative;background:var(--white);font-family:"Kumbh Sans",sans-serif;color:var(--text)}
.abs{position:absolute}
.center{left:0;width:1200px;text-align:center}

/* top bar */
.topbar{top:0;left:0;width:1200px;height:29px;background:var(--red);color:var(--white);font-size:11px}
.topbar .social-dot{position:absolute;left:130px;top:9px;width:10px;height:10px;border-radius:50%;background:var(--white)}
.topbar .mail{position:absolute;right:128px;top:8px;display:flex;align-items:center;gap:5px;font-family:"Roboto",sans-serif}

/* header */
.header{top:29px;left:0;width:1200px;height:61px;background:var(--white)}
.brand{position:absolute;left:130px;top:22px;display:flex;align-items:center;gap:7px;font-family:"Raleway",sans-serif;font-weight:700;font-size:14px;color:var(--red);line-height:1}
.brand .mark{width:14px;height:14px;background:var(--red)}
.nav{position:absolute;left:538px;top:24px;display:flex;gap:40px;font-family:"Roboto",sans-serif;font-size:11px;color:var(--ink)}
.nav .active{color:var(--red);position:relative}
.nav .active svg{position:absolute;left:10px;top:14px}
.donate{position:absolute;left:977px;top:16px;width:93px;height:29px;border-radius:15px;background:var(--red);color:var(--white);font-family:"Roboto",sans-serif;font-weight:500;font-size:11px;display:flex;align-items:center;justify-content:center}

/* hero */
.hero{top:90px;left:0;width:1200px;height:272px;background:linear-gradient(135deg,#5b5f5c,#4a4f4c 50%,#55574f)}
.hero-title{top:193px;font-family:"Raleway",sans-serif;font-weight:700;font-size:33px;color:var(--white);letter-spacing:.5px}
.hero-title span{color:var(--red)}
.crumb{top:241px;font-family:"Roboto",sans-serif;font-size:10px;color:#ddd}
.crumb b{font-weight:400;color:var(--white)}

/* headings */
.h-lg{font-family:"Raleway",sans-serif;font-weight:600;color:var(--ink)}
.kicker{font-family:"Raleway",sans-serif;font-weight:500;font-size:17px;color:var(--ink)}

/* info cards */
.card{position:absolute;top:523px;width:300px;height:164px;border:1px solid var(--line);text-align:center}
.card .icon{width:49px;height:49px;border-radius:50%;background:var(--red);margin:32px auto 0;display:flex;align-items:center;justify-content:center}
.card h3{margin-top:12px;font-family:"Raleway",sans-serif;font-weight:600;font-size:17px;color:var(--red)}
.card p{margin-top:6px;font-size:12px;color:var(--ink)}

/* form section */
.form-band{top:767px;left:0;width:1200px;height:558px;background:var(--soft)}
.field{position:absolute;border:1px solid var(--line);font-size:12px;color:var(--text);padding:22px 19px;background:var(--soft)}
.submit{position:absolute;left:404px;top:1212px;width:391px;height:57px;background:var(--red);color:var(--white);font-weight:600;font-size:12px;letter-spacing:1px;display:flex;align-items:center;justify-content:center}

/* team */
.member{position:absolute;top:1463px;width:175px;text-align:center}
.member .photo{width:175px;height:186px}
.member h4{margin-top:14px;font-family:"Raleway",sans-serif;font-weight:500;font-size:17px;color:var(--ink)}
.member p{margin-top:2px;font-size:11px;color:var(--muted)}

/* footer */
.footer-shape{top:0;left:0}
.foot-brand{position:absolute;left:130px;top:1898px;display:flex;align-items:center;gap:7px;font-family:"Raleway",sans-serif;font-weight:700;font-size:15px;color:var(--white)}
.foot-brand .mark{width:16px;height:16px;background:var(--white)}
.foot-about{position:absolute;left:130px;top:1955px;width:230px;font-size:11px;line-height:16px;color:#e6e6e6}
.foot-dot{position:absolute;left:130px;top:2020px;width:22px;height:22px;border-radius:50%;background:var(--red)}
.foot-col{position:absolute;top:1882px}
.foot-col h5{font-family:"Oswald",sans-serif;font-weight:500;font-size:16px;color:var(--red);letter-spacing:.3px}
.foot-col ul{list-style:none;margin-top:8px}
.foot-col li{font-size:11px;color:#e6e6e6;line-height:22.6px}
.contact-row{display:flex;gap:7px;align-items:flex-start;font-size:11px;color:#e6e6e6;line-height:14px;margin-bottom:14px}
.contact-row .ring{flex:none;width:23px;height:23px;border-radius:50%;border:1px solid #9aa;display:flex;align-items:center;justify-content:center}
.divider{top:2090px;left:130px;width:940px;border-top:1px dotted #555}
.copy{top:2114px;font-size:10.5px;color:var(--white)}
.copy span{color:var(--red)}
</style>
</head>
<body>

<div class="abs topbar">
  <span class="social-dot"></span>
  <div class="mail">
    <svg width="11" height="8" viewBox="0 0 11 8"><rect x=".5" y=".5" width="10" height="7" fill="none" stroke="#fff"/><polyline points=".5,.5 5.5,4.5 10.5,.5" fill="none" stroke="#fff"/></svg>
    hello@valpas-alliance.org
  </div>
</div>

<header class="abs header">
  <div class="brand"><span class="mark"></span>Valpas Alliance</div>
  <nav class="nav">
    <span>Home</span><span>Our Achievements</span><span>Media</span><span>Events</span>
    <span class="active">Contacts
      <svg width="28" height="8" viewBox="0 0 28 8"><polyline points="0,2 6,7 11,2 16,7 21,2 28,7" fill="none" stroke="#be1a27" stroke-width="1.3"/></svg>
    </span>
  </nav>
  <div class="donate">DONATE</div>
</header>

<section class="abs hero" role="img" aria-label="Dimmed regional map of the alpine valley around the association"></section>
<h1 class="abs center hero-title">CONTACT <span>US</span></h1>
<div class="abs center crumb">Home | <b>Contact</b></div>

<h2 class="abs center h-lg" style="top:420px;font-size:35px">Contact Info</h2>
<p class="abs center" style="top:474px;font-size:13px;color:var(--ink)">Sed ut perspiciatis unde omnis iste natus error sit voluptatem</p>

<div class="card" style="left:293px">
  <div class="icon"><svg width="14" height="20" viewBox="0 0 14 20"><path d="M7 0C3 0 0 3 0 7c0 5 7 13 7 13s7-8 7-13c0-4-3-7-7-7zm0 10a3 3 0 1 1 0-6 3 3 0 0 1 0 6z" fill="#fff"/></svg></div>
  <h3>Location</h3>
  <p>1870 Montbel - Valais - Switzerland</p>
</div>
<div class="card" style="left:607px">
  <div class="icon"><svg width="18" height="13" viewBox="0 0 18 13"><rect width="18" height="13" rx="1.5" fill="#fff"/><polyline points="1,1.5 9,7.5 17,1.5" fill="none" stroke="#be1a27" stroke-width="1.6"/></svg></div>
  <h3>Email</h3>
  <p>hello@valpas-alliance.org</p>
</div>

<section class="abs form-band"></section>
<div class="abs center kicker" style="top:818px">Get In Touch</div>
<h2 class="abs center h-lg" style="top:838px;font-size:36px">Have Any Question</h2>
<div class="field" style="left:203px;top:925px;width:392px;height:58px">Name:</div>
<div class="field" style="left:605px;top:925px;width:391px;height:58px">Phone:</div>
<div class="field" style="left:203px;top:994px;width:793px;height:58px">Email:</div>
<div class="field" style="left:203px;top:1062px;width:793px;height:138px">Comments:</div>
<div class="submit">SUBMIT</div>

<div class="abs center kicker" style="top:1375px">Committee</div>
<h2 class="abs center h-lg" style="top:1395px;font-size:36px">Our Team Member</h2>

<div class="member" style="left:130px"><div class="photo" role="img" aria-label="Portrait photo of Margarate Nobel" style="background:linear-gradient(160deg,#5d6b45,#9a6a4a)"></div><h4>Margarate Nobel</h4><p>Team Management</p></div>
<div class="member" style="left:322px"><div class="photo" role="img" aria-label="Portrait photo of Danial Offence" style="background:linear-gradient(160deg,#dcdcdc,#4d5038)"></div><h4>Danial Offence</h4><p>Management</p></div>
<div class="member" style="left:513px"><div class="photo" role="img" aria-label="Portrait photo of Pitbul Simmulate" style="background:linear-gradient(160deg,#c8ccd0,#2a2d33)"></div><h4>Pitbul Simmulate</h4><p>Team Management</p></div>
<div class="member" style="left:704px"><div class="photo" role="img" aria-label="Portrait photo of Alexa Gradian" style="background:linear-gradient(160deg,#9b9290,#b07a50 60%,#222)"></div><h4>Alexa Gradian</h4><p>Team Management</p></div>
<div class="member" style="left:894px"><div class="photo" role="img" aria-label="Portrait photo of Jhon Doe" style="background:linear-gradient(160deg,#7b7a55,#c9cdd8)"></div><h4>Jhon Doe</h4><p>Team Management</p></div>

<svg class="abs footer-shape" width="1200" height="2179" viewBox="0 0 1200 2179" aria-hidden="true" style="pointer-events:none">
  <polygon points="0,1773 471,1846 1200,1719 1200,2179 0,2179" fill="#262d30"/>
</svg>

<footer>
  <div class="foot-brand"><span class="mark"></span>Valpas Alliance</div>
  <p class="foot-about">Sed ut perspiciatis unde omnis iste<br>natus error sit voluptatem accusantium<br>rem aperiam</p>
  <span class="foot-dot"></span>

  <div class="foot-col" style="left:450px">
    <h5>SITEMAP</h5>
    <ul><li>Home</li><li>Our Achivements</li><li>Media</li><li>Events</li><li>Contact Us</li></ul>
  </div>
  <div class="foot-col" style="left:670px">
    <h5>OTHERS</h5>
    <ul><li>Privacy Policy</li><li>Terms &amp; Conditions</li><li>Leagal</li><li>Donate</li><li>Help / Support</li></ul>
  </div>
  <div class="foot-col" style="left:876px">
    <h5>CONTACTS</h5>
    <div style="margin-top:14px">
      <div class="contact-row"><span class="ring"><svg width="8" height="11" viewBox="0 0 14 20"><path d="M7 0C3 0 0 3 0 7c0 5 7 13 7 13s7-8 7-13c0-4-3-7-7-7zm0 10a3 3 0 1 1 0-6 3 3 0 0 1 0 6z" fill="#be1a27"/></svg></span><span>Route des Prés 12 / 1870<br>Montbel</span></div>
      <div class="contact-row" style="align-items:center"><span class="ring"><svg width="11" height="8" viewBox="0 0 18 13"><rect width="18" height="13" rx="1.5" fill="#be1a27"/><polyline points="1,1.5 9,7.5 17,1.5" fill="none" stroke="#262d30" stroke-width="1.6"/></svg></span><span>hello@valpas-alliance.org</span></div>
    </div>
  </div>

  <div class="abs divider"></div>
  <p class="abs center copy">Copyright © 2022 <span>Valpas Alliance</span>. All Rights Reserved.</p>
</footer>

</body>
</html>
```